Law Firm Needs Stationery Design and Business Cards

i would like some fresh new ideas for letterhead. current letterhead is attached. the bottom of the letterhead should have the same content as the bottom of the current letterhead. with the dagger (cross) symbol attached at the beginning and referenced by the two names at the top. see existing letterhead and this will make better sense.

use existing logo and content. nothing overly fancy. i like simple, classy, and refined. does not have to be same font on existing letterhead.

for envelopes, use logo and Raleigh, NC address only

Industry/Entity Type

Business

Contact Information for Business Card

Name: Dominic R. Halvey, Esq.

2784 Bramble Court, Suite 406
Raleigh, NC 27654

phone 919-555-0147
fax 919-555-0183
cell 919-555-0126

www.halveylegalpc.com
dom@halveylegalpc.com

```html
<!DOCTYPE html>
<html lang="en">
<head>
<meta charset="utf-8">
<title>Halvey Law — Business Card</title>
<link href="https://fonts.googleapis.com/css2?family=Cinzel:wght@600&family=Questrial&display=swap" rel="stylesheet">
<style>
  :root {
    --navy: #13237a;
    --navy-soft: #1b2d88;
    --slate: #8a8d94;
    --ink: #3f4147;
    --paper: #f4f4f2;
    --backdrop: #d9dadd;
    --white: #ffffff;
  }
  * { box-sizing: border-box; margin: 0; padding: 0; }
  html, body {
    width: 1200px;
    height: 789px;
    overflow: hidden;
    background: var(--backdrop);
  }
  .canvas {
    position: relative;
    width: 1200px;
    height: 789px;
    display: flex;
    align-items: center;
    justify-content: center;
    gap: 44px;
  }
  .card {
    position: relative;
    width: 500px;
    height: 286px;
    overflow: hidden;
  }
  .card--front { background: var(--navy); }
  .card--back { background: var(--paper); }

  .watermark {
    position: absolute;
    right: -70px;
    bottom: -90px;
    width: 330px;
    height: 330px;
  }

  .brand {
    position: absolute;
    display: flex;
    flex-direction: column;
    align-items: center;
    gap: 10px;
  }
  .card--front .brand {
    left: 50%;
    top: 50%;
    transform: translate(-50%, -50%);
  }
  .card--back .brand {
    left: 36px;
    top: 64px;
  }
  .brand__dot {
    width: 46px;
    height: 46px;
    border-radius: 50%;
    background: var(--slate);
  }
  .brand__name {
    font-family: "Cinzel", serif;
    font-weight: 600;
    font-size: 30px;
    letter-spacing: 1px;
    line-height: 1;
  }
  .card--front .brand__name { color: var(--white); }
  .card--back .brand__name { color: var(--navy); }

  .details {
    position: absolute;
    right: 30px;
    top: 58px;
    text-align: right;
    font-family: "Questrial", sans-serif;
    color: var(--ink);
  }
  .details__name {
    font-family: "Questrial", sans-serif;
    font-weight: 400;
    font-size: 14px;
    letter-spacing: 0.6px;
    color: var(--navy);
    text-transform: uppercase;
    -webkit-text-stroke: 0.4px var(--navy);
  }
  .details__credential {
    font-size: 11.5px;
    line-height: 1.4;
  }
  .details__contact {
    margin-top: 26px;
    font-size: 11.5px;
    line-height: 1.45;
    font-style: normal;
  }
  .details__label {
    color: var(--navy);
    font-weight: 700;
  }
</style>
</head>
<body>
  <main class="canvas">
    <section class="card card--front" aria-label="Business card front">
      <svg class="watermark" viewBox="0 0 330 330" aria-hidden="true">
        <circle cx="165" cy="165" r="150" fill="none" stroke="var(--navy-soft)" stroke-width="22"/>
      </svg>
      <div class="brand">
        <span class="brand__dot"></span>
        <span class="brand__name">Halvey Law</span>
      </div>
    </section>

    <section class="card card--back" aria-label="Business card back">
      <div class="brand">
        <span class="brand__dot"></span>
        <span class="brand__name">Halvey Law</span>
      </div>
      <div class="details">
        <h1 class="details__name">Dominic R. Halvey, Esq.</h1>
        <p class="details__credential">Licensed in NC and FL</p>
        <p class="details__credential">Board certified Civil trial specialist</p>
        <address class="details__contact">
          <span class="details__label">T:</span> 919.555.0147<br>
          <span class="details__label">F:</span> 919.555.0183<br>
          <span class="details__label">W:</span> www.halveylegalpc.com<br>
          2784 Bramble Court, Suite 406<br>
          Raleigh, NC 27654
        </address>
      </div>
    </section>
  </main>
</body>
</html>
```